Business Cards for Branding (Advertising) Agency

We need stylish and cool business cards.
Additional info:
1) Logo - see the attachment. You can use either the three penguins or just one penguin face (square or round) - at your discretion.
2) Text and other stuff for business card:
front side:
-Logo and company name: company name - Northern Walruses - should be in English as is in logo. This is the only exception. The rest of the text will be in Russian.
-Who we are: Брендинговое агентство
-First and last name:
-Position: Управляющий партнёр
-Address:
-Phone:
-Email:
-Website:
Note: please don't use names of information fields, such as: who we are, first and last name, position, address, phone, email and website.

3) Our suggestions on design:
-The backside of the business card can be either blank or has something on it - at your discretion.
-The business card background should be either white or grey (you can use any tone of grey).

Additional Information:
1) БРЕНДИНГОВОЕ АГЕНТСТВО
2) ул. Кедровская - these two words should be together on the same line
3) тел.: +7 (495) 381-96-02
моб.: +7 (916) 507-28-94

```html
<!DOCTYPE html>
<html lang="ru">
<head>
<meta charset="utf-8">
<title>Northern Walruses — визитная карточка</title>
<link rel="stylesheet" href="https://fonts.googleapis.com/css2?family=Roboto:wght@300;400;500&display=swap">
<style>
  :root {
    --bg: #e4e1dc;
    --card: #ffffff;
    --ink: #1a1a1a;
    --grey: #6f6f6f;
    --grey-light: #9a9a9a;
    --rule: #d2d2d2;
    --accent: #f29e12;
    --on-accent: #ffffff;
  }
  html, body {
    margin: 0;
    padding: 0;
    width: 1200px;
    height: 1000px;
    overflow: hidden;
    background: var(--bg);
    font-family: "Roboto", Arial, sans-serif;
  }
  .canvas {
    position: relative;
    width: 1200px;
    height: 1000px;
  }
  .card {
    position: absolute;
    left: 285px;
    width: 630px;
    height: 350px;
    background: var(--card);
    border-radius: 18px;
    overflow: hidden;
    box-shadow: 0 2px 6px rgba(0,0,0,.12);
  }
  .card--front { top: 110px; }
  .card--back { top: 540px; }

  /* Front */
  .brand {
    position: absolute;
    inset: 0;
    display: flex;
    align-items: center;
    justify-content: center;
    gap: 22px;
  }
  .brand__dot {
    width: 64px;
    height: 64px;
    border-radius: 50%;
    background: var(--ink);
  }
  .brand__name {
    font-weight: 400;
    font-size: 40px;
    letter-spacing: 6px;
    text-transform: uppercase;
    color: var(--ink);
    line-height: 1.1;
  }

  /* Back */
  .band {
    position: absolute;
    top: 0; left: 0; right: 0;
    height: 70px;
    background: var(--accent);
    color: var(--on-accent);
    display: flex;
    align-items: center;
    justify-content: space-between;
    padding: 0 30px;
    box-sizing: border-box;
  }
  .band__tagline {
    font-weight: 300;
    font-size: 23px;
  }
  .band__brand {
    display: flex;
    align-items: center;
    gap: 10px;
    font-weight: 300;
    font-size: 15px;
    letter-spacing: 2px;
    text-transform: uppercase;
  }
  .band__dot {
    width: 22px;
    height: 22px;
    border-radius: 50%;
    background: var(--on-accent);
  }
  .person {
    position: absolute;
    top: 92px;
    left: 30px;
  }
  .person__name {
    font-weight: 500;
    font-size: 24px;
    color: var(--accent);
    margin: 0;
  }
  .person__role {
    font-weight: 500;
    font-size: 18px;
    color: var(--grey);
    margin: 4px 0 0;
  }
  .rule {
    position: absolute;
    left: 30px;
    width: 330px;
    border: 0;
    margin: 0;
  }
  .rule--solid { top: 166px; border-top: 2px solid var(--rule); }
  .rule--dotted { top: 272px; border-top: 2px dotted var(--rule); }
  .contacts {
    position: absolute;
    top: 178px;
    left: 30px;
    margin: 0;
    padding: 0;
    list-style: none;
  }
  .contacts li {
    display: flex;
    align-items: center;
    gap: 10px;
    font-weight: 300;
    font-size: 17px;
    color: var(--grey);
    line-height: 29px;
  }
  .contacts svg { width: 14px; height: 14px; fill: var(--accent); }
  .address {
    position: absolute;
    top: 284px;
    left: 30px;
    font-style: normal;
    font-weight: 400;
    font-size: 17px;
    line-height: 26px;
    color: var(--ink);
  }
</style>
</head>
<body>
<main class="canvas">
  <section class="card card--front" aria-label="Лицевая сторона">
    <div class="brand">
      <span class="brand__dot"></span>
      <span class="brand__name">Northern<br>Walruses</span>
    </div>
  </section>

  <section class="card card--back" aria-label="Оборотная сторона">
    <header class="band">
      <span class="band__tagline">Брендинговое агентство</span>
      <span class="band__brand"><span class="band__dot"></span>Northern Walruses</span>
    </header>

    <div class="person">
      <p class="person__name">Мария Ласточкина</p>
      <p class="person__role">Управляющий партнёр</p>
    </div>

    <hr class="rule rule--solid">

    <ul class="contacts">
      <li>
        <svg viewBox="0 0 24 24" aria-hidden="true"><path d="M6.6 10.8a15.1 15.1 0 0 0 6.6 6.6l2.2-2.2c.3-.3.7-.4 1-.2 1.1.4 2.3.6 3.6.6.6 0 1 .4 1 1V20c0 .6-.4 1-1 1A17 17 0 0 1 3 4c0-.6.4-1 1-1h3.5c.6 0 1 .4 1 1 0 1.3.2 2.5.6 3.6.1.3 0 .7-.2 1z"/></svg>
        +7 (916) 507-28-94
      </li>
      <li>
        <svg viewBox="0 0 24 24" aria-hidden="true"><path d="M2 5h20v14H2zm2 2v.5l8 5 8-5V7zm0 2.8V17h16V9.8l-8 5z"/></svg>
        maria@northernwalruses.ru
      </li>
      <li>
        <svg viewBox="0 0 24 24" aria-hidden="true"><circle cx="5" cy="19" r="2.5"/><path d="M3 10a11 11 0 0 1 11 11h-3a8 8 0 0 0-8-8zm0-6a17 17 0 0 1 17 17h-3A14 14 0 0 0 3 7z"/></svg>
        www.northernwalruses.ru
      </li>
    </ul>

    <hr class="rule rule--dotted">

    <address class="address">
      115432, г. Москва<br>
      ул. Кедровская, д.12, стр.5
    </address>
  </section>
</main>
</body>
</html>
```